Modern Verdell Tree Care Website

I need a website for a full service Tree Care company. The company provides tree pruning, tree removal, tree preservation, emergency services, stump grinding, and emergency tree services.

Target Market(s)

Customers that need tree services

Industry/Entity Type

Landscaping, Tree Services

Coding

Coded - Design and coding required

Number of Pages Required

5+ page

Font styles to use
Sans Serif

Requirements
Must have
• Good clean design that showcases the services the company provides.
Nice to have
• Services page; contact form, blog, home page, about page

```html
<!DOCTYPE html>
<html lang="en">
<head>
<meta charset="utf-8">
<title>Verdell Tree Care</title>
<link href="https://fonts.googleapis.com/css2?family=Syncopate:wght@700&family=Poppins:ital,wght@0,300;0,400;0,500;0,600;0,700;1,400&display=swap" rel="stylesheet">
<style>
:root{
  --green:#8cc63f;
  --orange:#f7a934;
  --slate:#5b6770;
  --slate-band:#5f6b72;
  --ink:#2f2f2f;
  --text:#444;
  --beige:#d9c3a5;
  --card:#f5f5f5;
  --footer:#333333;
  --white:#fff;
}
*{box-sizing:border-box;margin:0;padding:0}
html,body{width:1200px;height:4870px;overflow:hidden}
body{position:relative;background:var(--white);font-family:'Poppins',sans-serif;color:var(--text)}
.abs{position:absolute}
.btn{position:absolute;display:flex;align-items:center;justify-content:center;border-radius:30px;color:var(--white);font-size:13px;font-weight:600;letter-spacing:.5px;text-transform:uppercase}
.btn-green{background:var(--green)}
.btn-orange{background:var(--orange)}

/* header */
.brand{position:absolute;display:flex;align-items:center;gap:12px;font-family:'Poppins',sans-serif;font-weight:700;font-size:26px;color:var(--slate);white-space:nowrap}
.brand-mark{width:34px;height:34px;background:var(--green)}
.nav{position:absolute;left:388px;top:48px;font-size:14px;font-weight:600;color:var(--ink)}
.nav span{position:absolute;white-space:nowrap}
.call{position:absolute;left:892px;top:14px}
.call-icon{position:absolute;left:0;top:26px;width:38px;height:38px;border-radius:50%;background:var(--green)}
.call-label{position:absolute;left:51px;top:5px;font-size:14px;font-weight:700;color:var(--ink);white-space:nowrap}
.call-num{position:absolute;left:51px;font-size:24px;font-weight:600;color:var(--orange);white-space:nowrap;line-height:1}

/* hero */
.hero{position:absolute;left:0;top:117px;width:1200px;height:668px;background:linear-gradient(160deg,#6f7a60 0%,#9aa08f 35%,#b9bcb3 55%,#5d6646 100%)}
.hero-text{position:absolute;left:0;width:1200px;text-align:center;color:var(--white);white-space:nowrap}
.dots{position:absolute;display:flex;gap:9px}
.dots i{width:10px;height:10px;border-radius:50%;background:var(--white);display:block}

/* about */
.about-img{position:absolute;left:75px;top:805px;width:382px;height:382px;background:linear-gradient(135deg,#a8873d,#6f8f3a 50%,#8cc63f)}
.h2{position:absolute;font-family:'Syncopate',sans-serif;font-weight:700;font-size:42px;line-height:1;color:var(--slate);white-space:nowrap}
.h2 .g{color:var(--green)}
.about p{position:absolute;left:524px;width:600px;font-size:13.5px;line-height:26px;color:var(--ink)}

/* services */
.svc{position:absolute;width:330px;height:354px;background:var(--card);border:1px solid #e8e8e8;border-radius:12px;overflow:hidden;text-align:center}
.svc-img{height:176px}
.svc h3{margin-top:26px;font-size:20px;font-weight:600;color:var(--orange);text-transform:uppercase}
.svc p{margin:14px auto 0;width:250px;font-size:13px;line-height:25px;color:var(--ink)}

/* why */
.why-label{position:absolute;color:var(--white);font-size:15px;font-weight:600;white-space:nowrap;letter-spacing:.3px}
.why-icon{position:absolute;width:58px;height:58px;margin:-29px 0 0 -29px;border-radius:50%;background:var(--slate);border:4px solid #e9ece6;display:flex;align-items:center;justify-content:center}

/* reviews */
.review{position:absolute;top:3056px;width:330px;height:265px;background:var(--card);border-radius:12px;text-align:center}
.review .q{margin-top:22px;height:38px;font-family:'Poppins',sans-serif;font-weight:700;font-size:64px;line-height:64px;color:var(--green)}
.review p{margin:6px auto 0;width:272px;font-size:13px;font-style:italic;line-height:24px;color:var(--ink)}
.review .who{margin-top:8px;font-size:14px;font-weight:600;color:var(--orange)}

/* gallery */
.gallery{position:absolute;left:0;top:3408px;width:1200px;height:387px;background:var(--slate-band)}
.gallery-tile{position:absolute;top:132px;width:252px;height:187px;border-radius:10px}

/* contact */
.info-row{position:absolute;left:75px}
.info-ico{position:absolute;left:0;top:0;width:38px;height:38px;border-radius:50%;border:1px solid var(--orange);display:flex;align-items:center;justify-content:center}
.info-row b{position:absolute;left:55px;top:-8px;font-size:18px;font-weight:600;color:var(--orange);white-space:nowrap}
.info-row span{position:absolute;left:55px;top:22px;font-size:15px;color:var(--ink);white-space:nowrap}
.form{position:absolute;left:616px;top:3861px;width:511px;height:424px;background:var(--green);border-radius:4px}
.field{position:absolute;background:var(--white);border-radius:24px;font-size:14px;color:#777;padding:13px 0 0 20px}

/* footer */
.foot{position:absolute;left:0;top:4357px;width:1200px;height:513px}
.fcol{position:absolute;top:4560px;color:var(--white);font-size:13px}
.fcol h4{font-size:14px;font-weight:700;margin-bottom:12px;letter-spacing:.3px}
.fcol div{line-height:30px;white-space:nowrap}
.social{position:absolute;left:75px;top:4745px;display:flex;gap:18px}
.social i{width:20px;height:20px;border-radius:50%;background:var(--white);display:block}
</style>
</head>
<body>

<!-- header -->
<div class="brand" style="left:75px;top:38px"><div class="brand-mark"></div>Verdell Tree Care</div>
<nav class="nav">
  <span style="left:0;color:var(--orange)">HOME</span>
  <span style="left:85px">ABOUT</span>
  <span style="left:179px">SERVICES</span>
  <span style="left:292px">BLOG</span>
  <span style="left:372px">CONTACT US</span>
</nav>
<div class="call">
  <div class="call-icon">
    <svg width="38" height="38" viewBox="0 0 38 38"><path d="M14 11c1 0 2 3 2.5 4.5.3 1-1.5 2-1.3 2.7.8 2 2.6 3.8 4.6 4.6.7.2 1.7-1.6 2.7-1.3 1.5.5 4.5 1.5 4.5 2.5 0 2-2 4-4 4-7 0-13-6-13-13 0-2 2-4 4-4z" fill="#fff"/></svg>
  </div>
  <div class="call-label">Call Us Today:</div>
  <div class="call-num" style="top:27px">(555) 214 7730,</div>
  <div class="call-num" style="top:57px">(555) 382 4416</div>
</div>

<!-- hero -->
<section class="hero" role="img" aria-label="Arborists in a bucket lift trimming a tall tree"></section>
<div class="hero-text" style="top:316px;font-size:44px;font-weight:300;letter-spacing:1px">WELCOME TO</div>
<div class="hero-text" style="top:358px;font-size:60px;font-weight:700;letter-spacing:1px">VERDELL TREE CARE</div>
<div class="hero-text" style="top:435px;font-size:35px;font-weight:700">WE ARE A FULL SERVICE TREE CARE COMPANY.</div>
<div class="btn btn-green" style="left:510px;top:507px;width:180px;height:45px">Contact Us</div>
<div class="dots" style="left:564px;top:660px"><i></i><i style="background:var(--orange)"></i><i></i><i></i></div>
<svg class="abs" style="left:0;top:715px" width="1200" height="72" viewBox="0 0 1200 72">
  <path d="M0 72 C40 35 90 3 190 3 L1070 3 C1140 3 1180 20 1200 45 L1200 72 Z" fill="#fff"/>
</svg>

<!-- about -->
<section class="about">
  <div class="about-img" role="img" aria-label="Arborist climbing a tree, framed in a triangular shape"></div>
  <div class="h2" style="left:524px;top:808px;font-size:38px;line-height:48px">ABOUT VERDELL<br><span class="g">TREE CARE</span></div>
  <p style="top:906px">At Verdell Tree Care, we are more than just a tree service company, we are stewards of our beautiful trees. With a passion deeply rooted in arboriculture, we embark on a mission to promote the health, beauty, and safety of your trees and landscapes.</p>
  <p style="top:1026px">Whether it's expert tree trimming to enhance aesthetics, meticulous tree removal to mitigate hazards, or comprehensive tree health assessments to ensure safety, we approach each task with unwavering dedication and attention to detail.</p>
  <div class="btn btn-orange" style="left:524px;top:1138px;width:180px;height:49px">Read More</div>
</section>

<!-- services -->
<section class="services">
  <div class="h2" style="left:0;top:1292px;width:1200px;text-align:center">OUR <span class="g">SERVICES</span></div>
  <div class="svc" style="left:75px;top:1370px"><div class="svc-img" role="img" aria-label="Arborist in orange pruning branches" style="background:linear-gradient(135deg,#b9c6cf,#6b7d55)"></div><h3>Tree Pruning</h3><p>Sed ut perspiciatis unde omnis iste natus error sit voluptatem accusa tium vitae dicta sunt explicabo.</p></div>
  <div class="svc" style="left:436px;top:1370px"><div class="svc-img" role="img" aria-label="Worker cutting a trunk with a chainsaw" style="background:linear-gradient(135deg,#3f5a2a,#7a6a4a)"></div><h3>Tree Removal</h3><p>Sed ut perspiciatis unde omnis iste natus error sit voluptatem accusa tium vitae dicta sunt explicabo.</p></div>
  <div class="svc" style="left:797px;top:1370px"><div class="svc-img" role="img" aria-label="Hands forming a heart on a mossy trunk" style="background:linear-gradient(135deg,#6b5a3a,#7f8f3d)"></div><h3>Tree Preservation</h3><p>Sed ut perspiciatis unde omnis iste natus error sit voluptatem accusa tium vitae dicta sunt explicabo.</p></div>
  <div class="svc" style="left:75px;top:1752px"><div class="svc-img" role="img" aria-label="Firefighter spraying water on a forest fire" style="background:linear-gradient(135deg,#e0621e,#5a3a22)"></div><h3>Emergency Services</h3><p>Sed ut perspiciatis unde omnis iste natus error sit voluptatem accusa tium vitae dicta sunt explicabo.</p></div>
  <div class="svc" style="left:436px;top:1752px"><div class="svc-img" role="img" aria-label="Tree stump being ground down" style="background:linear-gradient(135deg,#8a6b4a,#4c3b2a)"></div><h3>Stump Grinding</h3><p>Sed ut perspiciatis unde omnis iste natus error sit voluptatem accusa tium vitae dicta sunt explicabo.</p></div>
  <div class="svc" style="left:797px;top:1752px"><div class="svc-img" role="img" aria-label="Fallen tree across a green park" style="background:linear-gradient(135deg,#4f7a2e,#7fae45)"></div><h3>Emergency Tree Services</h3><p>Sed ut perspiciatis unde omnis iste natus error sit voluptatem accusa tium vitae dicta sunt explicabo.</p></div>
  <div class="btn btn-orange" style="left:510px;top:2172px;width:180px;height:47px">View All</div>
</section>

<!-- why choose us -->
<section class="why">
  <svg class="abs" style="left:0;top:2280px" width="1200" height="632" viewBox="0 0 1200 632">
    <path d="M0 80 C200 0 420 -10 620 30 S1000 100 1200 140 L1200 632 L0 632 Z" fill="var(--beige)"/>
    <path d="M0 112 C220 40 430 30 640 70 S1010 140 1200 175 L1200 632 L0 632 Z" fill="var(--green)"/>
    <path d="M335 632 A265 265 0 0 1 865 632" fill="none" stroke="#e9ece6" stroke-width="3"/>
    <path d="M388 632 A212 212 0 0 1 812 632 Z" fill="#fff"/>
  </svg>
  <div class="h2" style="left:0;top:2482px;width:1200px;text-align:center;font-size:40px;color:#fff">WHY CHOOSE US</div>
  <div class="brand" style="left:0;top:2810px;width:1200px;justify-content:center;font-size:22px"><div class="brand-mark" style="width:24px;height:24px"></div>Verdell Tree Care</div>

  <div class="why-label" style="left:0;width:1200px;text-align:center;top:2572px">PROFESSIONAL WORK</div>
  <div class="why-label" style="right:763px;top:2641px">LOCALLY OWNED &amp; OPERATED</div>
  <div class="why-label" style="left:767px;top:2641px">SAFETY IS OUR NO PRIORITY</div>
  <div class="why-label" style="right:845px;top:2724px">24-HOURS EMERGENCY SERVICES</div>
  <div class="why-label" style="left:852px;top:2724px">LICENSED ARBORIST ON STAFF</div>
  <div class="why-label" style="right:890px;top:2815px">LICENSED AND INSURED</div>
  <div class="why-label" style="left:907px;top:2815px">FREE ESTIMATES</div>

  <div class="why-icon" style="left:601px;top:2646px"><svg width="24" height="24" viewBox="0 0 24 24"><path d="M4 20C4 10 10 4 20 4c0 10-6 16-16 16zM4 20l9-9" fill="#fff" stroke="#5b6770" stroke-width="1.5"/></svg></div>
  <div class="why-icon" style="left:488px;top:2671px"><svg width="20" height="24" viewBox="0 0 20 24"><path d="M10 23S2 14 2 9a8 8 0 0 1 16 0c0 5-8 14-8 14z" fill="#fff"/><circle cx="10" cy="9" r="3" fill="#5b6770"/></svg></div>
  <div class="why-icon" style="left:714px;top:2671px"><svg width="20" height="22" viewBox="0 0 20 22"><path d="M10 1l8 3v6c0 6-4 10-8 11C6 20 2 16 2 10V4z" fill="#fff"/><path d="M10 4v14" stroke="#5b6770" stroke-width="2"/></svg></div>
  <div class="why-icon" style="left:403px;top:2735px"><svg width="24" height="24" viewBox="0 0 24 24"><circle cx="12" cy="12" r="10" fill="#fff"/><path d="M12 6v6l4 3" stroke="#5b6770" stroke-width="2" fill="none"/></svg></div>
  <div class="why-icon" style="left:799px;top:2735px"><svg width="28" height="20" viewBox="0 0 28 20"><circle cx="14" cy="6" r="4" fill="#fff"/><circle cx="5" cy="8" r="3" fill="#fff"/><circle cx="23" cy="8" r="3" fill="#fff"/><path d="M7 19c0-5 3-8 7-8s7 3 7 8zM0 19c0-4 2-6 5-6s4 1 4 2M28 19c0-4-2-6-5-6s-4 1-4 2" fill="#fff"/></svg></div>
  <div class="why-icon" style="left:350px;top:2826px"><svg width="20" height="24" viewBox="0 0 20 24"><path d="M2 1h11l5 5v17H2z" fill="#fff"/><path d="M6 11h8M6 15h8M6 19h5" stroke="#5b6770" stroke-width="1.6"/></svg></div>
  <div class="why-icon" style="left:850px;top:2826px"><svg width="22" height="22" viewBox="0 0 22 22"><rect x="1" y="1" width="20" height="20" rx="3" fill="#fff"/><path d="M6 16l1-4 7-7 3 3-7 7z" fill="#5b6770"/></svg></div>
</section>

<!-- reviews -->
<section class="reviews">
  <div class="h2" style="left:0;top:2975px;width:1200px;text-align:center">CUSTOMER <span class="g">REVIEWS</span></div>
  <div class="review" style="left:75px"><div class="q">”</div><p>Duis aute irure dolor in reprehenderit in voluptate velit esse cillum dolore eu fugiat nulla pariatur enim ipsam voluptatem quia voluptas sit aspernatur aut odit aut fugit, sed quia consequuntur magni dolores</p><div class="who">Dana, Millbrook, NJ</div></div>
  <div class="review" style="left:436px"><div class="q">”</div><p>Duis aute irure dolor in reprehenderit in voluptate velit esse cillum dolore eu fugiat nulla pariatur enim ipsam voluptatem quia voluptas sit aspernatur aut odit aut fugit, sed quia consequuntur magni dolores</p><div class="who">Dana, Millbrook, NJ</div></div>
  <div class="review" style="left:797px"><div class="q">”</div><p>Duis aute irure dolor in reprehenderit in voluptate velit esse cillum dolore eu fugiat nulla pariatur enim ipsam voluptatem quia voluptas sit aspernatur aut odit aut fugit, sed quia consequuntur magni dolores</p><div class="who">Dana, Millbrook, NJ</div></div>
  <div class="dots" style="left:572px;top:3350px"><i style="background:var(--green)"></i><i style="background:var(--slate)"></i><i style="background:var(--slate)"></i><i style="background:var(--slate)"></i></div>
</section>

<!-- gallery -->
<section class="gallery">
  <div class="abs" style="left:0;top:58px;width:1200px;text-align:center;color:#fff;font-size:30px;font-weight:500">Follow our latest work</div>
  <div class="gallery-tile" role="img" aria-label="Pole saw cutting a branch" style="left:75px;background:linear-gradient(135deg,#5d7a3a,#a6b58a)"></div>
  <div class="gallery-tile" role="img" aria-label="Climber harnessed in a tree" style="left:342px;background:linear-gradient(135deg,#c9d4b9,#5c7d33)"></div>
  <div class="gallery-tile" role="img" aria-label="Aerial lift beside a house among trees" style="left:609px;background:linear-gradient(180deg,#8fb3de,#7d8f55)"></div>
  <div class="gallery-tile" role="img" aria-label="Child hugging a tree in a sunny forest" style="left:875px;background:linear-gradient(135deg,#d9a65a,#4e6a2e)"></div>
</section>

<!-- address -->
<section class="contact">
  <div class="h2" style="left:75px;top:3898px;font-size:40px">ADDRESS</div>
  <p class="abs" style="left:75px;top:3964px;width:510px;font-size:14px;line-height:26px;color:var(--ink)">Sed ut perspiciatis unde omnis iste natus error sit voluptatem accusantium doloremque laudantium, totam rem aperiam, eaque ipsa quae ab illo inventore veritatis</p>
  <div class="info-row" style="top:4065px"><div class="info-ico"><svg width="16" height="16" viewBox="0 0 16 16"><path d="M2 8l6-5 6 5v6H2z" fill="var(--orange)"/></svg></div><b>Address</b><span>48 Alder Row, Brookfield Glen, NJ 07811</span></div>
  <div class="info-row" style="top:4131px"><div class="info-ico"><svg width="16" height="16" viewBox="0 0 16 16"><path d="M4 2c1 0 2 2 2 3 0 .8-1 1.2-.8 1.7.7 1.6 2 2.9 3.6 3.6.5.2.9-.8 1.7-.8 1 0 3 1 3 2 0 1.5-1.5 2.5-3 2.5C6 14 2 10 2 5c0-1.5 1-3 2-3z" fill="var(--orange)"/></svg></div><b>Phone No</b><span>(555) 214 7730, (555) 382 4416</span></div>
  <div class="info-row" style="top:4197px"><div class="info-ico"><svg width="16" height="16" viewBox="0 0 16 16"><rect x="1" y="3" width="14" height="10" rx="1" fill="var(--orange)"/><path d="M1 4l7 5 7-5" stroke="#fff" fill="none"/></svg></div><b>Email</b><span>info@verdelltreecare.com</span></div>

  <div class="form">
    <div class="h2" style="left:23px;top:34px;font-size:38px;color:#fff">CONTACT US</div>
    <div class="field" style="left:23px;top:97px;width:227px;height:47px">Name</div>
    <div class="field" style="left:257px;top:97px;width:231px;height:47px">Email&nbsp; Address</div>
    <div class="field" style="left:23px;top:159px;width:227px;height:47px">Phone No</div>
    <div class="field" style="left:257px;top:159px;width:231px;height:47px">Services
      <svg class="abs" style="right:18px;top:17px" width="8" height="12" viewBox="0 0 8 12"><path d="M4 0l4 5H0zM4 12L0 7h8z" fill="#555"/></svg></div>
    <div class="field" style="left:23px;top:220px;width:465px;height:109px">Message</div>
    <div class="btn btn-orange" style="left:23px;top:342px;width:179px;height:47px">Submit</div>
  </div>
</section>

<!-- footer -->
<footer>
  <svg class="foot" width="1200" height="513" viewBox="0 0 1200 513">
    <path d="M0 60 C200 10 420 -10 640 25 S1000 20 1200 0 L1200 513 L0 513 Z" fill="var(--beige)"/>
    <path d="M0 100 C220 40 430 20 650 55 S1010 50 1200 35 L1200 513 L0 513 Z" fill="var(--footer)"/>
  </svg>
  <div class="brand" style="left:75px;top:4614px;color:#fff;font-size:24px"><div class="brand-mark" style="width:30px;height:30px"></div>Verdell Tree Care</div>
  <div class="abs" style="left:75px;top:4675px;color:#fff;font-size:11px;line-height:22px">© Copyright 2024 Company Name<br>All Rights Reserved.</div>
  <div class="social" aria-label="Social media links"><i></i><i></i><i></i><i></i><i></i></div>
  <div class="fcol" style="left:374px"><h4>SITE MAP</h4><div>Home</div><div>About</div><div>Services</div><div>Blog</div><div>Contact Us</div></div>
  <div class="fcol" style="left:614px"><h4>SERVICES</h4><div>Tree pruning</div><div>Tree removal</div><div>Tree preservation</div><div>Emergency services</div><div>Stump grinding</div><div>Emergency tree services</div></div>
  <div class="fcol" style="left:886px"><h4>CONTACT US</h4><div style="line-height:24px">48 Alder Row,<br>Brookfield Glen, NJ 07811</div><div>(555) 608-1294</div><div>hello@verdelltreecare.com</div><h4 style="margin-top:22px">FOLLOW US</h4></div>
</footer>

</body>
</html>
```